real estate managers brochure A5

Real estate services brochure (owners corporation management)

Content has been uploaded in MS word documents and we reserve the right to refine the text in one revision.

Visit out site http://www.marrowfen.com.au/body-corporate-managers/ and review the pages in the 'owners corporation' menu in our website - the brochure is for these services we provide.

We want to showcase a variety of 'trophy' buildings/unit/apartment/factory developments that we manage - I've uploaded these 'case studies' and high res images for each.

Some General services photos to be provided by you.

The brochure is given out to potential owners who we wish to be clients.

We are going to print a few dozen of these in hard copy so will need artwork in nigh resolution pdf format and a web resolution version for emailing potential clients.

Target Market(s)

Unit owners, apartment owners and commercial factory owners

Industry/Entity Type

Property Management

Font styles to use
Serif
Sans Serif

Requirements
Must have
• A modern design that looks like it could be just as home on a website or facebook post
• Have a flair of retro design and/or vintage graphics
• 3 full pages of example properties we manage property. see example properties in the case studies. I have uploaded high res images for the full page images and some brief text for these pages
Should not have
• Must not look like a typical real estate agents brochure (smiling agents, happy home owners)
• Images of people who do not look australian (ie afro american, asian) as this is not our target market. We typically have anglo australian or eruopean looking clients
• We are a young company who pride ourselves on. Efficient services and high tech management systems for the properties we manage

```html
<!DOCTYPE html>
<html lang="en">
<head>
<meta charset="utf-8">
<title>Marrowfen – Owners Corporation Management Brochure</title>
<link href="https://fonts.googleapis.com/css2?family=Source+Sans+3:wght@400;600;700&display=swap" rel="stylesheet">
<style>
  :root {
    --navy: #2c45a0;
    --heading: #2a3f9e;
    --sky: #0aa3dc;
    --ink: #2b2b2b;
    --white: #ffffff;
    --panel: rgba(255,255,255,0.84);
  }
  * { margin: 0; padding: 0; box-sizing: border-box; }
  html, body { width: 1200px; height: 929px; overflow: hidden; background: #fff; }
  body { font-family: "Source Sans 3", sans-serif; color: var(--ink); }
  .spread { position: relative; width: 1200px; height: 929px; }

  .photo { position: absolute; }
  .photo-house-a { left: 0; top: 0; width: 600px; height: 352px;
    background: linear-gradient(180deg, #6fa3dc 0%, #a9c6e6 30%, #b58a62 62%, #6f6a4e 100%); }
  .photo-garden { left: 0; top: 352px; width: 316px; height: 200px;
    background: linear-gradient(180deg, #e6ecf2 0%, #8aa26a 50%, #6a7a3e 100%); }
  .photo-house-b { left: 316px; top: 352px; width: 284px; height: 200px;
    background: linear-gradient(180deg, #2f5fb0 0%, #8f7d70 45%, #3d5a32 75%, #2d55b0 100%); }
  .photo-townhouses { left: 0; top: 552px; width: 600px; height: 377px;
    background: linear-gradient(180deg, #4d86d4 0%, #c7d8ee 35%, #9a8f7e 65%, #cfc8bb 100%); }

  .pill { position: absolute; background: var(--navy); color: var(--white);
    border-radius: 22px; font-size: 14.5px; display: flex; align-items: center; justify-content: center; }
  .pill-top { left: 28px; top: 34px; width: 450px; height: 43px; }
  .pill-bottom { left: 295px; top: 845px; width: 260px; height: 43px; }

  .info-panel { position: absolute; background: var(--panel); padding: 12px 16px 0 28px; }
  .info-panel h2 { color: var(--heading); font-weight: 700; font-size: 18.5px; line-height: 1.05; text-transform: uppercase; margin-bottom: 22px; }
  .info-panel p { font-size: 14.5px; line-height: 1.08; }
  .panel-communities { left: 0; top: 242px; width: 357px; height: 176px; }
  .panel-case { left: 0; top: 607px; width: 246px; height: 280px; padding-top: 18px; padding-right: 10px; }
  .panel-case h2 { margin-bottom: 20px; }

  .services { position: absolute; left: 600px; top: 0; width: 600px; height: 929px; background: var(--white); }
  .band-top { height: 30px; background: var(--navy); }
  .dash { position: absolute; left: 0; right: 0; border-top: 2px dashed var(--navy); }
  .dash-top { top: 36px; }
  .dash-bottom { top: 770px; }
  .service-list { position: absolute; left: 41px; top: 58px; width: 520px; }
  .service h3 { color: var(--heading); font-weight: 400; font-size: 24.5px; line-height: 1.08; margin-bottom: 12px; }
  .service p { font-size: 14.5px; line-height: 1.2; }
  .service { margin-bottom: 12px; }
  .service.gap { margin-bottom: 22px; }

  .footer { position: absolute; left: 0; top: 777px; width: 600px; height: 152px; display: flex; }
  .footer-sites { width: 284px; background: var(--navy); color: var(--white); padding: 22px 0 0 41px; }
  .footer-sites h4 { font-weight: 400; font-size: 24px; margin-bottom: 14px; }
  .footer-sites .url { font-weight: 700; font-size: 15px; }
  .footer-sites .note { font-size: 14.5px; }
  .footer-partners { flex: 1; background: var(--sky); display: flex; align-items: center; color: var(--white); position: relative; }
  .partner-pay { width: 185px; text-align: center; font-size: 28px; font-weight: 700; letter-spacing: 4px; }
  .partner-divider { width: 1px; height: 96px; background: var(--white); }
  .partner-bank { flex: 1; display: flex; flex-direction: column; align-items: center; gap: 6px; font-size: 12px; font-weight: 600; text-transform: uppercase; }
  .partner-bank .mark { width: 54px; height: 54px; border-radius: 50%; background: var(--white); }
</style>
</head>
<body>
<div class="spread">
  <div class="photo photo-house-a" role="img" aria-label="Brick single-storey house with garage and garden in a gated community"></div>
  <div class="photo photo-garden" role="img" aria-label="Common garden with picnic shelter and shrubs"></div>
  <div class="photo photo-house-b" role="img" aria-label="Brick house at dusk with hedge and driveway"></div>
  <div class="photo photo-townhouses" role="img" aria-label="Street of new two-storey townhouses under a blue sky"></div>

  <div class="pill pill-top">48 Saltbush Road Mount Corrie. Gated community of 24 units</div>

  <div class="info-panel panel-communities">
    <h2>We manage residential communities</h2>
    <p>MARROWFEN manage an extensive range of residential units including gated townhouse communities. We work with the Committee or independently to ensure all common property is maintained to a high standard.</p>
  </div>

  <div class="info-panel panel-case">
    <h2>Case study –<br>townhouse<br>community</h2>
    <p>This property is a seaside townhouse community of 24 units. Prior to commencing construction, MARROWFEN was appointed by the developer to set up the owners corporation including placing competitive insurance and preparing budget and fee schedules.</p>
  </div>

  <div class="pill pill-bottom">1207 Tidewater Road, Ferndune</div>

  <section class="services">
    <div class="band-top"></div>
    <div class="dash dash-top"></div>
    <div class="service-list">
      <div class="service">
        <h3>Providing quality service since 2006</h3>
        <p>MARROWFEN is owned and operated by Harbourline Lifestyle Property Pty Ltd, an Australian corporation trading since 2006. We are located at modern offices in Corrington.</p>
      </div>
      <div class="service gap">
        <h3>Providing you with exceptional service</h3>
        <p>MARROWFEN offers a professional service with full quality control. We have experienced personnel, high tech systems, and well-organized procedures that we constantly improve.</p>
      </div>
      <div class="service">
        <h3>Representatives of Australia's leading owners corporation insurers</h3>
        <p>We deal directly with insurers so you have a single point of contact for claims and cut out the middle man brokers.</p>
      </div>
      <div class="service gap">
        <h3>Experienced and qualified</h3>
        <p>Marrowfen Estate Agents are qualified, highly skilled professionals with combined real estate experience of 20+ years.</p>
      </div>
      <div class="service gap">
        <h3>Adding value to owners corporation management</h3>
        <p>We'll guide you by managing the affairs of your owners corporation, ensuring compliance and proactively assisting you to improve your property.</p>
      </div>
      <div class="service">
        <h3>Easy to use payment systems</h3>
        <p>MARROWFEN offer a variety of ways to pay owners corporation contributions including BillDirect, Cheque, Cash, Eftpos and Credit Card using Keelbay Bank's TALLY payment systems.</p>
      </div>
    </div>
    <div class="dash dash-bottom"></div>

    <div class="footer">
      <div class="footer-sites">
        <h4>Websites</h4>
        <div class="url">www.marrowfen.com.au</div>
        <div class="note">Our main company site</div>
      </div>
      <div class="footer-partners">
        <div class="partner-pay">TALLY</div>
        <div class="partner-divider"></div>
        <div class="partner-bank">
          <div class="mark"></div>
          <span>Keelbay Bank</span>
        </div>
      </div>
    </div>
  </section>
</div>
</body>
</html>
```